Commercial Refrigeration Service Company requires stylish and fresh looking flyer.

We need a flyer to hand out to new customers. It should have a photo and our branding, list all the services that are offered and our contact details.
We would like two flyers to be supplied, both identical though one offering a discount until July ( Half Price Service Fee ). The flyer should be clear, interesting and in similar colours to the branding package supplied.
Please look at our website for information about the services on offer:
www.brisko-coolworks.com.au

Target Market(s)

Cafes, bars, restaurants, pubs ect.

Font styles to use
Other font styles liked:
• Font package provided

Colors
85cae6
ffffff
333333

Requirements
Must have
• - The photo provided.
• - The company logo.
• - Similar feel to the website & business card.
• - Smooth layout and clear to understand.
Should not have
• - No clunky badges or prints.

```html
<!DOCTYPE html>
<html lang="en">
<head>
<meta charset="utf-8">
<title>Brisko Coolworks Flyer</title>
<link href="https://fonts.googleapis.com/css2?family=Abel&family=Josefin+Sans:wght@300;400&family=Oswald:wght@500&display=swap" rel="stylesheet">
<style>
  :root {
    --brand-blue: #5bc2ec;
    --brand-dark: #2b2b2b;
    --text-dark: #333333;
    --icon-grey: #808285;
    --paper-top: #f4f4f4;
    --paper-bottom: #e5e5e5;
    --backdrop: #7b7b7b;
  }
  * { margin: 0; padding: 0; box-sizing: border-box; }
  html, body { width: 1200px; height: 1146px; overflow: hidden; }
  body { background: var(--backdrop); position: relative; }

  .flyer {
    position: absolute; left: 211px; top: 23px;
    width: 777px; height: 1100px;
    background: linear-gradient(var(--paper-top), var(--paper-bottom));
    box-shadow: 0 12px 24px rgba(0,0,0,.35);
    overflow: hidden;
  }
  .hero-photo {
    position: absolute; left: 0; top: 0; width: 777px; height: 291px;
    background: linear-gradient(180deg, #b9d3e6 0%, #9fb1bd 45%, #5f656d 75%, #c7bba8 100%);
  }
  .brand-band { position: absolute; left: 0; top: 291px; width: 777px; height: 284px; }

  .brand-lockup { position: absolute; left: 419px; top: 318px; width: 320px; text-align: center; color: var(--brand-dark); }
  .brand-name { font-family: 'Josefin Sans', sans-serif; font-weight: 300; font-size: 46px; letter-spacing: 28px; padding-left: 28px; line-height: 1; }
  .brand-dot { width: 14px; height: 14px; border: 1.5px solid var(--brand-dark); border-radius: 50%; margin: 26px auto 0; }
  .brand-tag-small { font-family: 'Josefin Sans', sans-serif; font-size: 11px; letter-spacing: 4px; margin-top: 36px; }
  .brand-tag-large { font-family: 'Josefin Sans', sans-serif; font-size: 19px; letter-spacing: 9px; margin-top: 10px; padding-left: 9px; }

  .offer { position: absolute; left: 46px; top: 482px; color: var(--brand-blue); font-family: 'Abel', sans-serif; }
  .offer-title { font-size: 32px; line-height: 1; letter-spacing: .5px; }
  .offer-sub { font-size: 15.5px; margin-top: 4px; }

  .services-heading {
    position: absolute; left: 0; top: 608px; width: 777px;
    display: flex; justify-content: center; align-items: center; gap: 6px;
    font-family: 'Oswald', sans-serif; font-weight: 500; font-size: 21px; color: var(--brand-blue);
  }
  .services-heading::before, .services-heading::after { content: ""; width: 64px; height: 2px; background: var(--brand-blue); }

  .service { position: absolute; transform: translateX(-50%); text-align: center; }
  .service-icon {
    width: 64px; height: 64px; margin: 0 auto; border-radius: 50%;
    background: var(--icon-grey); border: 2px solid var(--brand-blue);
    display: flex; align-items: center; justify-content: center;
  }
  .service-icon svg { width: 36px; height: 36px; fill: none; stroke: #fff; stroke-width: 1.6; stroke-linecap: round; stroke-linejoin: round; }
  .service-label { margin-top: 12px; font-family: 'Oswald', sans-serif; font-weight: 500; font-size: 19px; color: var(--brand-blue); white-space: nowrap; letter-spacing: -.2px; }

  .divider-marks { position: absolute; left: 0; top: 916px; width: 777px; display: flex; justify-content: center; gap: 34px; }
  .divider-marks span { width: 10px; height: 10px; border: 2px solid var(--brand-dark); transform: rotate(45deg); }

  .contact { position: absolute; left: 0; top: 949px; width: 777px; text-align: center; color: var(--text-dark); font-family: 'Abel', sans-serif; font-size: 17px; line-height: 20px; }
  .contact-web { font-family: 'Josefin Sans', sans-serif; font-weight: 400; font-size: 23px; letter-spacing: 2.5px; color: var(--brand-blue); margin-top: 6px; }

  .social-row { position: absolute; left: 0; top: 1046px; width: 777px; display: flex; justify-content: center; align-items: center; gap: 4px; }
  .social-row .rule { width: 36px; height: 2px; background: var(--brand-dark); margin: 0 2px; }
  .social-row .social-dot { width: 22px; height: 22px; border-radius: 50%; background: var(--brand-dark); }
</style>
</head>
<body>
<main class="flyer">
  <div class="hero-photo" role="img" aria-label="Photo of the technician standing beside the branded service ute at the beach"></div>

  <svg class="brand-band" viewBox="0 0 777 284" aria-hidden="true">
    <rect x="0" y="0" width="777" height="284" fill="var(--brand-dark)"/>
    <polygon points="0,0 777,0 777,248 419,248 340,175 0,175" fill="var(--brand-blue)"/>
  </svg>

  <div class="brand-lockup">
    <div class="brand-name">BRISKO</div>
    <div class="brand-dot"></div>
    <div class="brand-tag-small">COMMERCIAL</div>
    <div class="brand-tag-large">REFRIGERATION</div>
  </div>

  <div class="offer">
    <div class="offer-title">DISCOUNT UNTIL JULY</div>
    <div class="offer-sub">PAY ONLY HALF PRICE OF THE SERVICE FEE</div>
  </div>

  <h2 class="services-heading">OUR SERVICES</h2>

  <div class="service" style="left:192px; top:664px;">
    <div class="service-icon"><svg viewBox="0 0 36 36"><path d="M15 6a3 3 0 0 1 6 0v16a5 5 0 1 1-6 0z"/><circle cx="18" cy="26" r="2.5" fill="#fff"/><path d="M23 9h3M23 13h3M23 17h3"/></svg></div>
    <div class="service-label">COMMERCIAL REFRIGERATION</div>
  </div>
  <div class="service" style="left:366px; top:664px;">
    <div class="service-icon"><svg viewBox="0 0 36 36"><path d="M9 6h18l-2 25H11z"/><rect x="13" y="12" width="5" height="5"/><rect x="18" y="18" width="5" height="5"/><rect x="12" y="21" width="5" height="5"/></svg></div>
    <div class="service-label">ICE MAKERS</div>
  </div>
  <div class="service" style="left:507px; top:664px;">
    <div class="service-icon"><svg viewBox="0 0 36 36"><path d="M20 5l3 2-5 9"/><path d="M10 17h16v5H10z"/><path d="M18 22v5"/><path d="M18 29v2"/></svg></div>
    <div class="service-label">BEER SYSTEMS</div>
  </div>
  <div class="service" style="left:637px; top:664px;">
    <div class="service-icon"><svg viewBox="0 0 36 36"><path d="M21 5L11 20h7l-3 11 10-15h-7z"/></svg></div>
    <div class="service-label">ELECTRICAL</div>
  </div>
  <div class="service" style="left:252px; top:787px;">
    <div class="service-icon"><svg viewBox="0 0 36 36"><path d="M8 28L22 14"/><path d="M22 14a5 5 0 1 1 4 -8l-3 3 2 2 3-3a5 5 0 0 1-6 6"/><path d="M8 8l12 12"/><path d="M20 20l6 6-2 2-6-6"/></svg></div>
    <div class="service-label">24HR SERVICE</div>
  </div>
  <div class="service" style="left:381px; top:787px;">
    <div class="service-icon"><svg viewBox="0 0 36 36"><path d="M5 9h4l3 14h16l3-10H11"/><circle cx="14" cy="28" r="2"/><circle cx="25" cy="28" r="2"/></svg></div>
    <div class="service-label">SALES</div>
  </div>
  <div class="service" style="left:513px; top:787px;">
    <div class="service-icon"><svg viewBox="0 0 36 36"><path d="M8 24L24 8l4 4-16 16-5 1z"/><path d="M10 10l16 16-3 3L7 13z"/></svg></div>
    <div class="service-label">INSTALLATION</div>
  </div>

  <div class="divider-marks" aria-hidden="true"><span></span><span></span><span></span></div>

  <address class="contact" style="font-style:normal;">
    <div>PO Box 1180 Coolwater NSW 2099 | 0400 123 987</div>
    <div>info@brisko-coolworks.com.au | ABN: 12 345 678 901 | Licence No: 412275C</div>
    <div class="contact-web">WWW.BRISKO-COOLWORKS.COM.AU</div>
  </address>

  <div class="social-row" aria-label="Social media links">
    <span class="rule"></span>
    <span class="social-dot"></span>
    <span class="social-dot"></span>
    <span class="social-dot"></span>
    <span class="rule"></span>
  </div>
</main>
</body>
</html>
```